Quietly Lumenfold needs an eye catching marketing flyer

Our new Vantorelle Pulse(r) business needs an eye catching marketing flyer. We think A5 sizing?
website link (where you can understand more about breathwork is www.quietlylumenfold.co.uk)
Design whatever you would like to design some things that could be of use to mention are below. Will leave it in your capable hands.
Logo files for Quietly Lumenfold attached, use whichever one is best for your design, should be the main logo and colour scheme for the flyer, the second logo is that of Vantorelle Pulse(r) the breath school who's body of work we will be delivering. This can be anywhere on the flyer
Flyer is needed to get people interested in breathwork, the potential benefits for breathing better
We offer 1:1 sessions, workshops, corporate training
The flyer will have an offer code 'OpenDrift' which will give 15% off the bookers first 1:1 session
Flyer should include the following contact details: Maybe a "find out how breathwork can help you today. . . "
Greta Polworth (South): 07700 900 318
Danielle Crouse (Midlands): 07700 900 752
facebook: we.are.quietlylumenfold
instagram: _quietlylumenfold_

```html
<!DOCTYPE html>
<html lang="en">
<head>
<meta charset="utf-8">
<title>Quietly Lumenfold – Breathwork Flyer</title>
<link rel="stylesheet" href="https://fonts.googleapis.com/css2?family=Montserrat:wght@500;600;800&family=Jost:wght@300;500;600;700&family=Caveat:wght@600&display=swap">
<style>
  :root {
    --page-bg: #e6e8e9;
    --night: #061119;
    --teal-night: #1f4a5b;
    --ink: #1d4a57;
    --sky: #4aaee0;
    --leaf: #6a9a3e;
    --ember: #e8540f;
    --white: #ffffff;
    --band-blue: #2a52d6;
    --band-violet: #7b4fe6;
  }
  * { margin: 0; padding: 0; box-sizing: border-box; }
  html, body {
    width: 1200px; height: 1197px; overflow: hidden;
    background: var(--page-bg);
  }
  .flyer {
    position: absolute; left: 205px; top: 38px;
    width: 1015px; height: 1440px;
    transform: scale(0.7778); transform-origin: top left;
    overflow: hidden;
    background: var(--white);
    font-family: "Montserrat", sans-serif;
  }
  .flyer-art { position: absolute; inset: 0; }
  .txt { position: absolute; line-height: 1; white-space: nowrap; }

  .brand-name {
    left: 125px; top: 200px; width: 240px; text-align: center;
    color: var(--white); font-weight: 600; font-size: 30px; line-height: 1.2;
    white-space: normal;
  }

  .offer-intro { left: 72px; top: 790px; font-family: "Caveat", cursive; font-weight: 600; font-size: 92px; color: var(--ink); }
  .services { left: 66px; top: 893px; color: var(--ink); font-weight: 800; }
  .services span { display: block; line-height: 1; }
  .services .big { font-size: 51px; margin-bottom: 3px; }
  .services .small { font-size: 28.5px; margin-left: 10px; }

  .cta { left: 84px; top: 1066px; color: var(--sky); font-weight: 800; font-size: 34px; }
  .cta span { display: block; line-height: 0.99; }

  .contact { left: 84px; font-weight: 600; }
  .contact .name { display: block; font-size: 22px; }
  .contact .phone { display: block; font-size: 33px; font-weight: 800; margin-top: 4px; }
  .contact-south { top: 1193px; color: var(--leaf); }
  .contact-midlands { top: 1272px; color: var(--ember); }

  .offer-badge { left: 453px; width: 534px; text-align: center; color: var(--white); font-family: "Jost", sans-serif; }
  .offer-label { top: 650px; font-weight: 300; font-size: 66px; }
  .offer-code { top: 717px; font-weight: 700; font-size: 58px; }
  .offer-amount { top: 773px; font-weight: 700; font-size: 90px; }
  .offer-terms { top: 852px; font-weight: 600; font-size: 44px; }
  .offer-session { top: 895px; font-weight: 600; font-size: 66px; }

  .social { right: 40px; color: var(--white); font-weight: 500; font-size: 21px; display: flex; align-items: center; gap: 8px; }
  .social .dot { width: 18px; height: 18px; border-radius: 50%; background: var(--white); display: inline-block; }
  .social-insta { top: 1224px; }
  .social-face { top: 1252px; }
  .address { right: 40px; text-align: right; color: var(--white); font-weight: 500; }
  .address span { display: block; }
  .address .line1 { font-size: 18px; }
  .address .line2 { font-size: 26px; margin-top: 4px; }
  .address { top: 1297px; }
  .web { right: 40px; top: 1365px; color: var(--white); font-weight: 800; font-size: 30px; }
</style>
</head>
<body>
<main class="flyer">
  <svg class="flyer-art" width="1015" height="1440" viewBox="0 0 1015 1440" aria-hidden="false">
    <defs>
      <linearGradient id="night-sweep" x1="0" y1="0" x2="1" y2="0">
        <stop offset="0" stop-color="#061119"/>
        <stop offset="1" stop-color="#1f4a5b"/>
      </linearGradient>
      <linearGradient id="band-sweep" x1="0" y1="0" x2="1" y2="0">
        <stop offset="0" stop-color="#7b4fe6"/>
        <stop offset="0.5" stop-color="#2a52d6"/>
        <stop offset="1" stop-color="#7b4fe6"/>
      </linearGradient>
      <linearGradient id="forest-tones" x1="0" y1="0" x2="1" y2="0">
        <stop offset="0" stop-color="#3c6736"/>
        <stop offset="0.3" stop-color="#8fb3b3"/>
        <stop offset="0.55" stop-color="#c8dde2"/>
        <stop offset="0.8" stop-color="#567f4c"/>
        <stop offset="1" stop-color="#2f5a2f"/>
      </linearGradient>
      <linearGradient id="fade-white" x1="0" y1="0" x2="0" y2="1">
        <stop offset="0" stop-color="#ffffff" stop-opacity="0"/>
        <stop offset="1" stop-color="#ffffff"/>
      </linearGradient>
      <linearGradient id="badge-fill" x1="0" y1="0" x2="0" y2="1">
        <stop offset="0" stop-color="#8fd6ea"/>
        <stop offset="0.45" stop-color="#1e55d0"/>
        <stop offset="0.75" stop-color="#3d55d9"/>
        <stop offset="1" stop-color="#7c4fe8"/>
      </linearGradient>
      <radialGradient id="badge-shadow">
        <stop offset="0" stop-color="#000" stop-opacity="0.35"/>
        <stop offset="1" stop-color="#000" stop-opacity="0"/>
      </radialGradient>
    </defs>

    <rect class="photo-area" role="img" aria-label="Aerial photo of a forest with misty lung-shaped clearings" x="0" y="100" width="1015" height="640" fill="url(#forest-tones)"/>
    <rect x="0" y="600" width="1015" height="142" fill="url(#fade-white)"/>

    <path class="header-band" d="M0 326 C80 365 170 395 280 390 C430 382 520 260 640 170 C760 85 900 95 1015 160" fill="none" stroke="url(#band-sweep)" stroke-width="14"/>
    <path class="header" d="M0 0 H1015 V150 C900 85 760 78 640 160 C520 250 430 372 280 380 C170 386 80 356 0 316 Z" fill="url(#night-sweep)"/>

    <circle class="brand-ring" cx="245" cy="228" r="96" fill="none" stroke="#2a7fd0" stroke-width="2"/>

    <ellipse cx="720" cy="1068" rx="240" ry="20" fill="url(#badge-shadow)"/>
    <circle class="offer-disc" cx="720" cy="800" r="268" fill="url(#badge-fill)"/>
    <circle cx="720" cy="800" r="262" fill="none" stroke="#6fc6ec" stroke-opacity="0.5" stroke-width="6"/>

    <path class="footer-band" d="M0 1345 C100 1395 200 1420 300 1410 C450 1392 600 1190 720 1120 C820 1065 920 1110 1015 1172" fill="none" stroke="url(#band-sweep)" stroke-width="14"/>
    <path class="footer" d="M0 1358 C100 1405 200 1425 300 1415 C450 1398 600 1200 720 1132 C820 1078 920 1122 1015 1186 V1440 H0 Z" fill="url(#night-sweep)"/>
  </svg>

  <div class="txt brand-name">Quietly Lumenfold</div>

  <div class="txt offer-intro">We offer</div>
  <div class="txt services">
    <span class="big">1:1 SESSIONS</span>
    <span class="big">WORKSHOPS</span>
    <span class="small">CORPORATE TRAINING</span>
  </div>

  <div class="txt cta">
    <span>FIND OUT HOW</span>
    <span>BREATHWORK CAN</span>
    <span>HELP YOU TODAY. . .</span>
  </div>

  <div class="txt contact contact-south">
    <span class="name">Greta Polworth (South)</span>
    <span class="phone">07700 900 318</span>
  </div>
  <div class="txt contact contact-midlands">
    <span class="name">Danielle Crouse (Midlands)</span>
    <span class="phone">07700 900 318</span>
  </div>

  <div class="txt offer-badge offer-label">OFFER CODE</div>
  <div class="txt offer-badge offer-code">OPENDRIFT</div>
  <div class="txt offer-badge offer-amount">15% OFF</div>
  <div class="txt offer-badge offer-terms">THE BOOKERS FIRST</div>
  <div class="txt offer-badge offer-session">1:1 SESSION</div>

  <div class="txt social social-insta">@quietlylumenfold <span class="dot"></span></div>
  <div class="txt social social-face">/we.are.quietlylumenfold <span class="dot"></span></div>
  <div class="txt address">
    <span class="line1">14 FENWICK ROAD, HALVERSTONE.</span>
    <span class="line2">WEST MIDLANDS, HV10 4QZ</span>
  </div>
  <div class="txt web">QUIETLYLUMENFOLD.CO.UK</div>
</main>
</body>
</html>
```